Music Marketing Agency in need of a fully responsive website

Need a website for our music marketing agency with a nice Rev slider has the ability to take payments has a section with our work and client able to see case studies able to download our media kit in PDF can take appointments has social media and a careers upload section. Also want a prominent contact form. Nice and icons for music industry. I want them to be able to download a free Picsandra marketing download Very clean and not large icons or menu at the top very minimal menu bar this will have to go with our logo as well which I will add to order. I want this to be a membership oriented site. so there will be packages displayed or a membership form which they can use to sign up and need a login window. Also need to be able to put Tunevox playlist on the website. Save a section for past clients logos.Again this has to be a clean concept I would like pictures of Quellos such as an app promotion. Definitely want lots of flash words in bold letters across the pages when they scroll through new sections.
Updates

Need extra days to review

Target Market(s)

Urban Music

Coding

Coded - Design and coding required

Font styles to use
Serif

Colors

Designer to choose colors to be used in the design.

Requirements
Must have
• Please Add Logos attached at the Footer

```html
<!DOCTYPE html>
<html lang="en">
<head>
<meta charset="UTF-8">
<title>Cityvale Media – Login</title>
<link href="https://fonts.googleapis.com/css2?family=Montserrat:wght@600;700&family=Poppins:wght@400;500;600&display=swap" rel="stylesheet">
<style>
  :root {
    --brand-green: #21a67f;
    --ink: #1f1f1f;
    --text: #2b2b2b;
    --muted: #6b6b6b;
    --field-border: #c9c9c9;
    --icon: #a9a9a9;
    --white: #ffffff;
    --photo-dark: #2a2624;
    --photo-mid: #4a3f3a;
    --photo-warm: #5a2b2b;
  }
  * { box-sizing: border-box; margin: 0; padding: 0; }
  html, body {
    width: 1200px;
    height: 622px;
    overflow: hidden;
    background: var(--white);
  }
  .login-page {
    position: relative;
    width: 1200px;
    height: 622px;
    display: flex;
    font-family: "Poppins", Arial, sans-serif;
  }
  .login-panel {
    position: relative;
    width: 414px;
    height: 100%;
    background: var(--white);
  }
  .login-title {
    position: absolute;
    left: 53px;
    top: 172px;
    font-family: "Montserrat", Arial, sans-serif;
    font-weight: 700;
    font-size: 21px;
    letter-spacing: 0.2px;
    color: var(--ink);
  }
  .login-title .accent { color: var(--brand-green); }
  .login-form {
    position: absolute;
    left: 53px;
    top: 222px;
    width: 304px;
  }
  .field {
    position: relative;
    display: flex;
    align-items: center;
    height: 38px;
    border: 1px solid var(--field-border);
    margin-bottom: 10px;
    padding-left: 27px;
  }
  .field-icon {
    position: absolute;
    left: 10px;
    top: 50%;
    transform: translateY(-50%);
    width: 10px;
    height: 11px;
    fill: var(--icon);
  }
  .field-input {
    border: none;
    outline: none;
    width: 100%;
    font-family: "Poppins", Arial, sans-serif;
    font-size: 11.5px;
    color: var(--text);
    background: transparent;
  }
  .field-input::placeholder { color: var(--muted); }
  .login-button {
    display: block;
    width: 100%;
    height: 37px;
    margin-top: 2px;
    border: none;
    background: var(--brand-green);
    color: var(--white);
    font-family: "Poppins", Arial, sans-serif;
    font-weight: 600;
    font-size: 13px;
    letter-spacing: 0.3px;
    cursor: pointer;
  }
  .forgot-link {
    display: inline-block;
    margin-top: 10px;
    font-size: 12px;
    color: var(--text);
    text-decoration: none;
  }
  .copyright {
    position: absolute;
    left: 53px;
    top: 532px;
    font-size: 12.5px;
    color: var(--text);
  }
  .hero-panel {
    position: relative;
    flex: 1;
    height: 100%;
    background:
      radial-gradient(ellipse at 20% 30%, rgba(120, 40, 40, 0.55), transparent 55%),
      radial-gradient(ellipse at 70% 40%, rgba(150, 140, 130, 0.35), transparent 60%),
      linear-gradient(180deg, var(--photo-mid) 0%, var(--photo-dark) 60%, #3b3733 100%);
  }
  .hero-photo {
    position: absolute;
    inset: 0;
  }
  .brand-name {
    position: absolute;
    left: 0;
    right: 0;
    top: 286px;
    text-align: center;
    padding-left: 0;
    font-family: "Montserrat", Arial, sans-serif;
    font-weight: 700;
    font-size: 37px;
    letter-spacing: -0.5px;
    color: var(--white);
  }
</style>
</head>
<body>
  <main class="login-page">
    <section class="login-panel">
      <h1 class="login-title"><span class="accent">LOGIN</span> FORM</h1>
      <form class="login-form">
        <label class="field">
          <svg class="field-icon" viewBox="0 0 10 11" aria-hidden="true">
            <circle cx="5" cy="3" r="2.6"/>
            <path d="M0 11c0-3 2.2-4.8 5-4.8S10 8 10 11z"/>
          </svg>
          <input class="field-input" type="text" placeholder="User Name">
        </label>
        <label class="field">
          <svg class="field-icon" viewBox="0 0 10 11" aria-hidden="true">
            <path d="M2.4 5V3.4a2.6 2.6 0 0 1 5.2 0V5H6.4V3.4a1.4 1.4 0 0 0-2.8 0V5z"/>
            <rect x="1" y="5" width="8" height="6" rx="0.8"/>
          </svg>
          <input class="field-input" type="password" placeholder="Password">
        </label>
        <button class="login-button" type="submit">LOGIN</button>
        <a class="forgot-link" href="#">Forgot Password</a>
      </form>
      <p class="copyright">Copyrights @ 2018. All Rights Reserved.</p>
    </section>
    <section class="hero-panel">
      <div class="hero-photo" role="img" aria-label="Photo of a creative team gathered in a studio office, reviewing printed layouts spread on the floor"></div>
      <p class="brand-name">CITYVALE MEDIA</p>
    </section>
  </main>
</body>
</html>
```